Agriculture Security Company needs a business card design

We need a business card design for a new company based in Seattle calls Ferncrest Guardline LLC. We provide high-end physical security solutions that is geared and focused towards to the marijuana grow operations, wholesalers and distributors. We DO NOT get involved in the retail operations (store fronts). We would like to see designs that incorporate professionalism, reliability, trustworthy and forward thinking as traits of our organization.

Industry/Entity Type

Security

```html
<!DOCTYPE html>
<html lang="en">
<head>
<meta charset="utf-8">
<title>Ferncrest Guardline LLC – Business Card</title>
<link rel="stylesheet" href="https://fonts.googleapis.com/css2?family=Source+Sans+3:wght@400;600;700&display=swap">
<style>
  :root {
    --green-deep: #146a38;
    --green-mid: #2f8a3e;
    --green-light: #7db043;
    --green-pale: #e7f0e2;
    --ink: #4a4f4c;
    --paper: #ffffff;
    --backdrop: #ecebe6;
    --rule: #cfd3cf;
  }
  * { box-sizing: border-box; margin: 0; padding: 0; }
  html, body {
    width: 1200px; height: 1023px; overflow: hidden;
    background: var(--backdrop);
    font-family: "Source Sans 3", "Source Sans Pro", Arial, sans-serif;
  }
  .sheet {
    width: 1200px; height: 1023px;
    display: flex; flex-direction: column; align-items: center; justify-content: center;
    gap: 60px;
  }
  .card {
    position: relative;
    width: 700px; height: 400px;
    border-radius: 4px;
    overflow: hidden;
    box-shadow: 0 6px 18px rgba(0,0,0,0.18);
  }

  /* front */
  .card-front { background: var(--paper); }
  .front-band { position: absolute; inset: 0; }
  .brand-name {
    position: absolute; left: 56px; top: 92px;
    font-size: 40px; font-weight: 700; line-height: 1.05;
    color: var(--green-deep);
  }
  .front-rule {
    position: absolute; left: 56px; top: 218px;
    width: 420px; height: 1px; background: var(--rule);
  }
  .contact-list {
    position: absolute; left: 56px; top: 236px;
    list-style: none;
    font-size: 17px; color: var(--ink); line-height: 27px;
  }
  .contact-list li { display: flex; align-items: center; gap: 10px; }
  .contact-list svg { width: 15px; height: 15px; flex: none; }
  .person {
    position: absolute; right: 48px; top: 46px; text-align: right;
  }
  .person-name {
    font-size: 36px; font-weight: 700; color: var(--green-deep); line-height: 1.1;
  }
  .person-title {
    font-size: 18px; color: var(--green-light); margin-top: 2px;
  }
  .address {
    position: absolute; right: 48px; top: 152px; text-align: right;
    font-size: 18px; color: var(--ink); line-height: 26px;
  }
  .band-company {
    position: absolute; right: 40px; bottom: 22px;
    font-size: 17px; font-weight: 600; color: var(--paper);
  }

  /* back */
  .card-back { background: var(--green-deep); }
  .back-url {
    position: absolute; left: 0; right: 0; top: 38px; text-align: center;
    font-size: 16px; letter-spacing: 4px; color: #d9e8d6;
  }
  .back-brand {
    position: absolute; left: 0; right: 0; top: 168px; text-align: center;
    font-size: 56px; font-weight: 700; color: var(--paper);
  }
</style>
</head>
<body>
<main class="sheet">

  <section class="card card-front" aria-label="Business card front">
    <svg class="front-band" viewBox="0 0 700 400" preserveAspectRatio="none" aria-hidden="true">
      <path d="M0 400 L0 372 C 240 360, 520 330, 700 230 L700 400 Z" fill="var(--green-light)"/>
      <path d="M0 400 L0 380 C 250 372, 530 345, 700 252 L700 400 Z" fill="var(--green-deep)"/>
    </svg>

    <div class="brand-name">Ferncrest<br>Guardline</div>

    <div class="front-rule"></div>
    <ul class="contact-list">
      <li>
        <svg viewBox="0 0 16 16" aria-hidden="true"><path d="M4 1.5 L6.5 5 L5 6.5 C5.8 8.3 7.7 10.2 9.5 11 L11 9.5 L14.5 12 L13 14.5 C7 14.5 1.5 9 1.5 3 Z" fill="var(--green-deep)"/></svg>
        206-555-0148
      </li>
      <li>
        <svg viewBox="0 0 16 16" aria-hidden="true"><rect x="1" y="3" width="14" height="10" rx="1" fill="var(--green-deep)"/><path d="M1.5 3.8 L8 9 L14.5 3.8" stroke="#fff" stroke-width="1.3" fill="none"/></svg>
        info@ferncrestguardline.com
      </li>
      <li>
        <svg viewBox="0 0 16 16" aria-hidden="true"><circle cx="8" cy="8" r="7" fill="var(--green-deep)"/><path d="M1 8 H15 M8 1 C4.5 4.5 4.5 11.5 8 15 M8 1 C11.5 4.5 11.5 11.5 8 15" stroke="#fff" stroke-width="1" fill="none"/></svg>
        www.ferncrestguardline.com
      </li>
    </ul>

    <div class="person">
      <div class="person-name">Dana Whitlow</div>
      <div class="person-title">President</div>
    </div>
    <div class="address">1820 Alder Crest Rd<br>Seattle, WA 98109</div>

    <div class="band-company">Ferncrest Guardline LLC</div>
  </section>

  <section class="card card-back" aria-label="Business card back">
    <div class="back-url">www.ferncrestguardline.com</div>
    <div class="back-brand">Ferncrest Guardline</div>
  </section>

</main>
</body>
</html>
```